Window Treatment business needs website redesigned.

We need a revamp and refresh of our current site www.velmarix.ca
Looking to attract very high end customer. It should be a very simple design with very little text. This site will be visited by prospective homeowners, designers, builders and architects. They should feel that they are dealing with a high-end product selection, where experience, customer service and unique product offering is the focus. The content will be to highlight our services and highlight the manufacturers we sell, using a few rich photos to highlight the products. We should NOT look like we are a very large company. It should NOT have discounts/savings buttons and many menus to choose from. We offer over 15 years experience to narrow the many market options, to provide the right technical solution.
We specialize in products that are not readily available on the market and specifically motorized systems for indoors and outdoors.
Our main suppliers are Kravenholt.com, Dimbrell.com
We carry our own locally manufactured product line of roller shades.
Main product pictures should be of roller shades, outdoor bug screens, awnings and outdoor pergolas.

Reason: I understand that Christmas is coming up real short and many people are extremely busy. If you have a CREATIVE gifting you still want to submit, I look forward to your idea!

Reason: Due to holiday season, we have not had sufficient time to review to make a final decision. Thank you for your patience!

Target Market(s)

High end home owners, designers, builders, architects

Industry/Entity Type

Contractor

Coding

Coded - Design and coding required

Number of Pages Required

3 page

Font styles to use
Sans Serif

Requirements
Must have
• Landing page with full size image like homepage of zolvane.it
• Products page that highlights products with simple product shot image, description and link to manufacturer.
• On main page a scrolling of customer reviews.
• I want a very simple, eye-catching, emotional image for homepage. It does not need to include any product image.
• An image that shows technology combining/meshing with hand craftsmanship.
• Focus is on design.
• http://www.zolvane.it/en/gallery is a great layout and design.
Nice to have
• Logo shape for icons and watermark should be used.
• Look like and have simple motion effects like quorix.com or telvarin.com
Should not have
• Generic/standard looking feel like bluppet.com or mecklorwindow.ca
• No use of green as background only subtle text.
• Lots of text and pages.

```html
<!DOCTYPE html>
<html lang="en">
<head>
<meta charset="utf-8">
<title>Velmarix – Awnings</title>
<link rel="stylesheet" href="https://fonts.googleapis.com/css2?family=Montserrat:wght@400;500;600;700&display=swap">
<style>
  :root {
    --green: #6fb43f;
    --ink: #111111;
    --muted: #6a6a6a;
    --paper: #ffffff;
    --mist: #f6f7f7;
    --frame: rgba(255,255,255,0.82);
  }
  * { box-sizing: border-box; margin: 0; padding: 0; }
  html, body { width: 1200px; height: 929px; overflow: hidden; background: var(--paper); }
  body { font-family: "Montserrat", sans-serif; position: relative; }

  .hero { position: absolute; left: 0; top: 0; width: 1200px; height: 619px; overflow: hidden; }
  .hero-photo {
    position: absolute; inset: 0;
    background:
      linear-gradient(160deg, rgba(150,95,40,0.85) 0%, rgba(190,130,65,0.75) 30%, rgba(120,160,200,0.0) 55%),
      linear-gradient(180deg, #7ea6cc 0%, #a9c3d8 45%, #7d9a6a 62%, #5d8249 80%, #4c6a3a 100%);
  }
  .hero-frame {
    position: absolute; left: 16px; top: 12px; width: 1167px; height: 594px;
    border: 5px solid var(--frame);
  }
  .menu-button {
    position: absolute; left: 0; top: 35px; width: 58px; height: 49px;
    background: var(--green); display: flex; flex-direction: column;
    justify-content: center; align-items: center; gap: 6px;
  }
  .menu-button span { width: 22px; height: 2px; background: #fff; display: block; }
  .brand {
    position: absolute; left: 58px; top: 35px; width: 195px; height: 49px;
    background: var(--paper); display: flex; align-items: center; gap: 9px; padding-left: 13px;
  }
  .brand-mark { width: 16px; height: 16px; border-radius: 50%; background: var(--ink); }
  .brand-name { font-size: 22px; font-weight: 500; color: var(--ink); letter-spacing: 0.5px; }

  .hero-copy { position: absolute; left: 0; top: 258px; width: 1200px; text-align: center; color: #fff; }
  .hero-title { font-size: 62px; font-weight: 700; letter-spacing: 1px; line-height: 80px; }
  .hero-sub { font-size: 23px; font-weight: 400; line-height: 30px; margin-top: 2px; }

  .slider-dots { position: absolute; top: 560px; left: 0; width: 1200px; display: flex; justify-content: center; gap: 13px; }
  .slider-dots span { width: 9px; height: 9px; border: 1.5px solid #fff; border-radius: 50%; }

  .partners { position: absolute; left: 0; top: 619px; width: 1200px; height: 253px; background: var(--mist); }
  .partners-title { position: absolute; top: 43px; width: 100%; text-align: center; font-size: 26px; font-weight: 700; color: var(--ink); }
  .partners-title em { font-style: normal; color: var(--green); }
  .partners-rule { position: absolute; left: 0; width: 1200px; border-top: 1.5px dashed #8cc56a; }
  .partners-rule.top { top: 116px; }
  .partners-rule.bottom { top: 212px; }
  .partner-name {
    position: absolute; left: 412px; top: 150px; width: 140px;
    font-size: 19px; font-weight: 700; color: #555; letter-spacing: 1px; text-align: center;
  }
  .partner-badge { position: absolute; left: 688px; top: 137px; width: 58px; height: 58px; border-radius: 50%; border: 2px solid #999; background: #eee; }

  .footer { position: absolute; left: 0; top: 872px; width: 1200px; height: 57px; background: var(--paper); }
  .copyright { position: absolute; top: 27px; width: 100%; text-align: center; font-size: 11px; color: var(--muted); }
  .page-code { position: absolute; top: 26px; left: 1119px; font-size: 11px; color: #888; }
</style>
</head>
<body>
  <header class="hero">
    <div class="hero-photo" role="img" aria-label="Terrace with a large retractable awning overlooking a lake and green hills"></div>
    <div class="hero-frame"></div>
    <div class="menu-button" aria-label="Menu"><span></span><span></span><span></span></div>
    <div class="brand"><span class="brand-mark"></span><span class="brand-name">Velmarix</span></div>
    <div class="hero-copy">
      <h1 class="hero-title">Awnings</h1>
      <p class="hero-sub">Modern wind and rain Systems with<br>aluminium of fabric root systems</p>
    </div>
    <div class="slider-dots"><span></span><span></span><span></span><span></span></div>
  </header>

  <section class="partners">
    <h2 class="partners-title">Industry <em>Partners</em></h2>
    <div class="partners-rule top"></div>
    <div class="partner-name">KRAVENHOLT</div>
    <div class="partner-badge" role="img" aria-label="Partner badge"></div>
    <div class="partners-rule bottom"></div>
  </section>

  <footer class="footer">
    <p class="copyright">Copyrights © 2017, www.companyname.com . All Rights Reserved.</p>
    <span class="page-code">M1</span>
  </footer>
</body>
</html>
```